Bold Flyer Needed for Bold Little Gym

We need a 1 page flyer created for our small boutique fitness facility, CorVanto, which highlights a new service we are offering.
We are now offering Red Light Therapy (RLT) to our members and I need a full color, 1 page flyer created that captures the eye of our members while highlighting the benefits and clearly stating the prices at the bottom of the page.
Flyer will be printed out on a standard 8.5" x 11" sheet of paper and should be laid out in a way that is easy to read. Landscape or Portrait layouts are both expectable.
We are using Silverline Glow Therapy Lights LumaCore 700 Lamps as found here http://lnk.example/7QWRT5Z
I have attached the text that should be included and our logo for branding of the flyer.
Thank you!

```html
<!DOCTYPE html>
<html lang="en">
<head>
<meta charset="utf-8">
<title>CorVanto Red Light Therapy Flyer</title>
<link href="https://fonts.googleapis.com/css2?family=Anton&family=Oswald:wght@500;700&family=Montserrat:wght@300;700;800&family=Open+Sans:wght@400;600;700&family=Great+Vibes&family=Spectral:wght@400&family=Titillium+Web:ital,wght@0,700;1,700&display=swap" rel="stylesheet">
<style>
  :root {
    --bg: #f2f2f4;
    --ink: #1a0606;
    --wine: #2a0708;
    --red: #e0202b;
    --red-deep: #9b1218;
    --yellow: #f7d20c;
    --pale-yellow: #f3e08a;
    --white: #ffffff;
    --navy: #1b222b;
    --blue: #1ea7e6;
  }
  * { box-sizing: border-box; margin: 0; padding: 0; }
  html, body { width: 1200px; height: 845px; overflow: hidden; background: var(--bg); }
  .page {
    position: absolute; width: 440px; height: 572px; overflow: hidden;
    background: var(--ink); color: var(--white);
    font-family: "Open Sans", sans-serif;
  }
  .page--front { left: 149px; top: 127px;
    background: radial-gradient(ellipse at 30% 55%, #5a0d10 0%, #2a0708 45%, #140404 100%); }
  .page--back { left: 620px; top: 126px; background: #1a0506; }
  .abs { position: absolute; }

  /* front */
  .photo-model { left: 0; top: 40px; width: 175px; height: 532px;
    background: radial-gradient(ellipse at 50% 40%, #b3262a 0%, #6e1216 45%, rgba(40,6,8,0) 80%); }
  .photo-panel { left: 340px; top: 80px; width: 84px; height: 405px; border-radius: 3px;
    background: linear-gradient(90deg, #ff5a4a 0%, #e02a28 55%, #5a0a0c 60%, #3a0608 100%); }
  .headline { left: 184px; top: 30px; font-family: "Montserrat", sans-serif; font-weight: 300;
    font-size: 23px; line-height: 27px; }
  .headline b { font-weight: 700; }
  .headline .brand-inline { font-family: "Anton", sans-serif; font-weight: 400; color: var(--yellow);
    font-size: 34px; line-height: 42px; }
  .intro { left: 186px; top: 212px; color: var(--yellow); font-family: "Montserrat", sans-serif;
    font-weight: 800; font-size: 25px; line-height: 25px; }
  .intro .script { display: block; font-family: "Great Vibes", cursive; font-weight: 400; color: var(--white);
    font-size: 36px; line-height: 34px; margin: 2px 0 4px; }
  .transform { left: 186px; top: 381px; width: 130px; font-family: "Spectral", serif;
    color: var(--pale-yellow); font-size: 11.5px; line-height: 15px; }
  .badge { left: 316px; top: 390px; width: 100px; height: 100px; border-radius: 50%;
    background: var(--yellow); border: 4px solid var(--blue); color: #111;
    font-family: "Oswald", sans-serif; font-weight: 700; text-align: center;
    display: flex; flex-direction: column; justify-content: center; line-height: 1; }
  .badge span:nth-child(1) { font-size: 19px; }
  .badge span:nth-child(2) { font-size: 11.5px; margin: 2px 0; }
  .badge span:nth-child(3) { font-size: 19px; }
  .brand { font-family: "Anton", sans-serif; color: var(--white); letter-spacing: 1px; line-height: 1; }
  .brand--front { left: 26px; top: 458px; font-size: 58px; }
  .tagline { font-family: "Montserrat", sans-serif; font-weight: 700; color: var(--yellow);
    letter-spacing: 2.6px; white-space: nowrap; }
  .tagline--front { left: 66px; top: 525px; font-size: 8px; }
  .offer { right: 25px; top: 500px; text-align: right; font-family: "Oswald", sans-serif;
    font-weight: 500; line-height: 1.1; }
  .offer .line1 { font-size: 13px; }
  .offer .line2 { font-size: 18px; font-weight: 700; }
  .offer .line3 { font-family: "Titillium Web", sans-serif; font-style: italic; font-size: 15px; }

  /* back */
  .red-band { left: 0; top: 0; }
  .photo-client { left: 0; top: 240px; width: 232px; height: 332px;
    background: radial-gradient(ellipse at 40% 40%, #d2262c 0%, #7a1216 45%, #2a0607 85%); }
  .side { left: 242px; top: 0; width: 198px; height: 572px;
    background: radial-gradient(circle at 70% 40%, #2a333e 0%, var(--navy) 55%, #141a21 100%); }
  .contact { left: 32px; top: 24px; font-family: "Montserrat", sans-serif; font-weight: 300;
    font-size: 16.5px; line-height: 20px; }
  .contact .phone { font-family: "Titillium Web", sans-serif; font-weight: 700; color: var(--yellow);
    font-size: 23px; line-height: 26px; margin-top: 2px; }
  .contact .note { font-family: "Titillium Web", sans-serif; font-style: italic; font-weight: 700;
    font-size: 11.5px; line-height: 14px; }
  .brand--back { left: 32px; top: 122px; font-size: 90px; }
  .tagline--back { left: 86px; top: 211px; font-size: 10.5px; letter-spacing: 3.4px; }
  .heading { font-family: "Titillium Web", sans-serif; font-weight: 700; color: var(--yellow);
    font-size: 10px; line-height: 12px; }
  .about { left: 258px; top: 24px; width: 172px; }
  .about p { font-size: 6.9px; line-height: 9.1px; margin-top: 3px; color: #e6e6e6; }
  .benefits { left: 250px; top: 244px; width: 184px; }
  .benefits ul { list-style: none; margin-top: 5px; }
  .benefits li { position: relative; padding-left: 10px; font-size: 5.6px; line-height: 7px;
    margin-bottom: 4.3px; color: #e6e6e6; }
  .benefits li svg { position: absolute; left: 1px; top: 1px; }
  .why { left: 249px; top: 384px; width: 184px; }
  .why ul { list-style: none; margin-top: 4px; }
  .why li { position: relative; padding-left: 10px; font-size: 5.5px; line-height: 6.9px;
    margin-bottom: 2.4px; color: #e6e6e6; }
  .why li::before { content: ""; position: absolute; left: 1px; top: 2px; width: 5px; height: 5px;
    border-radius: 50%; background: #f5a623; }
  .motto { left: 251px; top: 464px; font-family: "Titillium Web", sans-serif; font-style: italic;
    font-weight: 700; color: var(--yellow); font-size: 11.3px; line-height: 14.5px; }
  .prices { left: 248px; top: 499px; width: 178px; border-collapse: collapse; font-size: 6px;
    color: var(--white); }
  .prices th { background: var(--red-deep); font-family: "Titillium Web", sans-serif; font-size: 7.5px;
    height: 12px; text-align: center; }
  .prices th:first-child, .prices td:first-child { text-align: left; padding-left: 4px; }
  .prices td { height: 10px; text-align: center; }
  .prices tr:nth-child(odd) td { background: var(--red); }
  .prices tr:nth-child(even) td { background: #b3151d; }
  .prices th + th, .prices td + td { border-left: 1px solid rgba(255,255,255,.6); }
  .ring { left: 73px; top: 363px; width: 166px; height: 166px; border-radius: 50%;
    border: 1px solid rgba(255,255,255,.8); }
  .promo { left: 80px; top: 370px; width: 152px; height: 152px; border-radius: 50%;
    background: var(--yellow); color: #111; text-align: center; font-family: "Open Sans", sans-serif; }
  .promo .title { font-family: "Titillium Web", sans-serif; font-weight: 700; font-size: 17px;
    line-height: 19px; margin-top: 15px; }
  .promo .body { font-size: 8.3px; line-height: 11.5px; margin-top: 5px; padding: 0 4px; }
  .promo .ask { font-size: 15px; line-height: 17px; margin-top: 4px; }
  .promo .ask span { display: block; font-size: 22px; line-height: 24px; }
</style>
</head>
<body>

<section class="page page--front">
  <div class="abs photo-model" role="img" aria-label="Photo of a woman posing in red light"></div>
  <div class="abs photo-panel" role="img" aria-label="Photo of a red light therapy panel"></div>

  <h1 class="abs headline">Unlock Your<br>Potential with<br><b>RED LIGHT<br>THERAPY</b> at<br><span class="brand-inline">CorVanto!</span></h1>

  <h2 class="abs intro">Introducing<span class="script">Our New</span>RED LIGHT<br>THERAPY<br>ROOM !</h2>

  <p class="abs transform">Transform Your Wellness Routine with the Power of Light!</p>

  <div class="abs badge"><span>SPECIAL</span><span>INTRODUCTORY</span><span>OFFER!</span></div>

  <div class="abs brand brand--front">CorVanto</div>
  <div class="abs tagline tagline--front">PERSONAL GROUP TRAINING</div>

  <div class="abs offer">
    <div class="line1">Try your first session</div>
    <div class="line2">for Just $25!</div>
    <div class="line3">(Regularly $55)</div>
  </div>
</section>

<section class="page page--back">
  <div class="abs photo-client" role="img" aria-label="Photo of a woman relaxing beside a red light therapy panel"></div>
  <svg class="abs red-band" width="245" height="572" viewBox="0 0 245 572" aria-hidden="true">
    <polygon points="213,0 242,0 242,572 230,572 230,122 213,110" fill="#e0202b"/>
    <polygon points="213,110 230,122 230,572 224,572 224,126 213,118" fill="#7a0f13"/>
  </svg>
  <div class="abs side"></div>

  <div class="abs contact">
    Visit our front<br>desk or call us at
    <div class="phone">(555) 214-3087</div>
    <div class="note">to schedule your appointment.</div>
  </div>

  <div class="abs brand brand--back">CorVanto</div>
  <div class="abs tagline tagline--back">PERSONAL GROUP TRAINING</div>

  <div class="abs about">
    <h3 class="heading">What is Red Light Therapy?</h3>
    <p>Red Light Therapy (RLT) is a revolutionary treatment that uses specific wavelengths of light to promote healing, reduce inflammation, and enhance overall well-being. At CorVanto, we are excited to offer the advanced Silverline Glow Therapy LumaCore 700 panels - designed to maximize your health benefits in a relaxing environment.</p>
  </div>

  <div class="abs benefits">
    <h3 class="heading">Benefits of Red Light Therapy</h3>
    <ul>
      <li><svg width="6" height="5" viewBox="0 0 6 5"><path d="M0.5 2.5 L2.2 4.2 L5.5 0.6" stroke="#e0202b" stroke-width="1.2" fill="none"/></svg>BOOSTS ENERGY LEVELS:<br>Feel revitalized and more energetic after each session.</li>
      <li><svg width="6" height="5" viewBox="0 0 6 5"><path d="M0.5 2.5 L2.2 4.2 L5.5 0.6" stroke="#e0202b" stroke-width="1.2" fill="none"/></svg>ENHANCES MUSCLE RECOVERY:<br>Speed up recovery times post-workout and reduce soreness.</li>
      <li><svg width="6" height="5" viewBox="0 0 6 5"><path d="M0.5 2.5 L2.2 4.2 L5.5 0.6" stroke="#e0202b" stroke-width="1.2" fill="none"/></svg>IMPROVES SKIN HEALTH:<br>Reduce wrinkles, blemishes, and promote a youthful glow.</li>
      <li><svg width="6" height="5" viewBox="0 0 6 5"><path d="M0.5 2.5 L2.2 4.2 L5.5 0.6" stroke="#e0202b" stroke-width="1.2" fill="none"/></svg>SUPPORTS JOINT HEALTH:<br>Alleviate pain and inflammation, making movement easier.</li>
      <li><svg width="6" height="5" viewBox="0 0 6 5"><path d="M0.5 2.5 L2.2 4.2 L5.5 0.6" stroke="#e0202b" stroke-width="1.2" fill="none"/></svg>PROMOTES BETTER SLEEP:<br>Improve your sleep patterns and overall restfulness.</li>
      <li><svg width="6" height="5" viewBox="0 0 6 5"><path d="M0.5 2.5 L2.2 4.2 L5.5 0.6" stroke="#e0202b" stroke-width="1.2" fill="none"/></svg>INCREASES CIRCULATION:<br>Enhance blood flow for better nutrient delivery to muscles.</li>
    </ul>
  </div>

  <div class="abs why">
    <h3 class="heading">Why Choose CorVanto?</h3>
    <ul>
      <li>State-of-the-Art Equipment: Experience the power of eight Silverline Glow Therapy LumaCore 700 panels—some of the best on the market!</li>
      <li>Expert Guidance: Our trained staff will guide you through each session to ensure you get the most out of your therapy.</li>
      <li>Community Focused: Join a supportive community that prioritizes health and wellness.</li>
    </ul>
  </div>

  <div class="abs motto">CorVanto Fitness Facility<br>Your Wellness, Our Commitment!</div>

  <table class="abs prices">
    <thead>
      <tr><th>PRICES:</th><th>CorVanto Member</th><th>Non-Member</th></tr>
    </thead>
    <tbody>
      <tr><td>Single Session</td><td>$35</td><td>$55</td></tr>
      <tr><td>3 - Pack</td><td>$102</td><td>$159</td></tr>
      <tr><td>5 - Pack</td><td>$167</td><td>$259</td></tr>
      <tr><td>10 - Pack</td><td>$316</td><td>$491</td></tr>
    </tbody>
  </table>

  <div class="abs ring"></div>
  <div class="abs promo">
    <div class="title">Limited<br>Time Only!</div>
    <div class="body">Book your session today and discover how Red Light Therapy can elevate your fitness journey.</div>
    <div class="ask">Ready to<span>Shine?</span></div>
  </div>
</section>

</body>
</html>
```